New Webpage for High Class Expert Witness Services Company

We are looking for a minimalist design for a webpage that just has our logo and an entry form offer to connect with one of our Liaisons.
The entry form should just ask for Name, Email, Contact Info and Description of Project.

Company Name is: The Marlowe Crest Advisory Services

Number of Pages Required

1 page

```html
<!DOCTYPE html>
<html lang="en">
<head>
<meta charset="utf-8">
<title>Marlowe Crest Advisory Services — Connect with a Liaison</title>
<link rel="stylesheet" href="https://fonts.googleapis.com/css2?family=Cinzel:wght@400;600;700&family=Roboto:wght@400&display=swap">
<style>
  :root {
    --bg: #000000;
    --ink: #ffffff;
    --ink-soft: #b9b9b9;
    --ink-muted: #a6a6a6;
    --frame: #8a8a8a;
    --field-border: #cfcfcf;
    --button-light: #e4e4e6;
    --button-mid: #d2d2d4;
    --button-dark: #a5a5a8;
    --button-ink: #111111;
  }
  * { box-sizing: border-box; margin: 0; padding: 0; }
  html, body {
    width: 1200px;
    height: 742px;
    overflow: hidden;
    background: var(--bg);
  }
  .page {
    position: relative;
    width: 1200px;
    height: 742px;
    overflow: hidden;
    background: var(--bg);
    color: var(--ink);
    font-family: "Roboto", Arial, sans-serif;
  }
  .mesh-texture {
    position: absolute;
    left: 460px;
    top: 170px;
    width: 740px;
    height: 572px;
    background:
      radial-gradient(ellipse 60% 55% at 78% 62%, rgba(120,120,120,0.30), rgba(60,60,60,0.12) 55%, rgba(0,0,0,0) 80%);
  }
  .brand {
    position: absolute;
    left: 124px;
    top: 46px;
    display: flex;
    align-items: center;
    gap: 14px;
  }
  .brand-mark {
    width: 34px;
    height: 34px;
    border: 2px solid var(--ink-soft);
  }
  .brand-name {
    font-family: "Cinzel", "Times New Roman", serif;
    font-weight: 600;
    font-size: 22px;
    letter-spacing: 1.5px;
    color: var(--ink-soft);
    line-height: 1.1;
  }
  .hero {
    position: absolute;
    left: 134px;
    top: 221px;
  }
  .hero-eyebrow {
    margin-left: 7px;
    font-family: "Cinzel", "Times New Roman", serif;
    font-size: 15px;
    letter-spacing: 2.2px;
    color: var(--ink-muted);
  }
  .hero-title {
    margin-top: 24px;
    font-family: "Cinzel", "Times New Roman", serif;
    font-weight: 400;
    font-size: 56px;
    line-height: 51px;
    letter-spacing: 1px;
    color: var(--ink);
  }
  .liaison-card {
    position: absolute;
    left: 714px;
    top: 123px;
    width: 380px;
    height: 438px;
    border: 1px solid var(--frame);
    padding: 36px 0 0 46px;
  }
  .liaison-title {
    font-family: "Cinzel", "Times New Roman", serif;
    font-weight: 400;
    font-size: 22px;
    letter-spacing: 0.5px;
    color: var(--ink);
    margin-bottom: 16px;
  }
  .liaison-form { display: flex; flex-direction: column; }
  .field {
    width: 294px;
    height: 42px;
    border: 1px solid var(--field-border);
    background: transparent;
    color: var(--ink);
    font-family: "Roboto", Arial, sans-serif;
    font-size: 13px;
    padding: 0 16px;
    margin-bottom: 12px;
    outline: none;
  }
  .field::placeholder { color: var(--ink); opacity: 1; }
  .field-area {
    height: 88px;
    padding-top: 12px;
    resize: none;
    margin-top: 2px;
  }
  .submit-button {
    width: 297px;
    height: 44px;
    margin-top: 1px;
    border: none;
    background: linear-gradient(115deg, var(--button-light) 0%, var(--button-mid) 45%, var(--button-light) 62%, var(--button-dark) 100%);
    color: var(--button-ink);
    font-family: "Cinzel", "Times New Roman", serif;
    font-weight: 700;
    font-size: 15px;
    letter-spacing: 0.5px;
    cursor: pointer;
  }
  .legal {
    position: absolute;
    left: 124px;
    top: 634px;
    font-size: 12px;
    line-height: 19px;
    color: var(--ink-muted);
  }
</style>
</head>
<body>
  <main class="page">
    <div class="mesh-texture" role="img" aria-label="Faint grey geometric network mesh backdrop"></div>

    <header class="brand">
      <span class="brand-mark" aria-hidden="true"></span>
      <span class="brand-name">Marlowe Crest<br>Advisory Services</span>
    </header>

    <section class="hero">
      <p class="hero-eyebrow">MARLOWE CREST ADVISORY SERVICES</p>
      <h1 class="hero-title">SEAMLESS<br>MEDICAL EXPERT<br>INTEGRATION</h1>
    </section>

    <section class="liaison-card">
      <h2 class="liaison-title">Connect with a Liaison</h2>
      <form class="liaison-form">
        <input class="field" type="text" placeholder="Name*" aria-label="Name">
        <input class="field" type="email" placeholder="Email*" aria-label="Email">
        <input class="field" type="tel" placeholder="Phone number*" aria-label="Phone number">
        <textarea class="field field-area" placeholder="Description of Project" aria-label="Description of Project"></textarea>
        <button class="submit-button" type="submit">SUBMIT</button>
      </form>
    </section>

    <footer class="legal">
      © 2026 Marlowe Crest Advisory Services.<br>All Rights Reserved
    </footer>
  </main>
</body>
</html>
```